Business Card Design For A Renovation Contractor Company

We need a business card for a new company based in Singapore, our company name is "RB Tolvane". We are a renovation contractor that builds designs into reality. We build more of F&B restaurants, retail stores and commercial offices. We work very closely with designers. The final design should communicate to our client that we are a company that you can trust, that will plan and complete your project without giving you a headache. I like my client to remember my company as "RB". The beauty of SIMPLE is important.

Industry/Entity Type

Contractor

Requirements
Nice to have
• Black or Red base

```html
<!DOCTYPE html>
<html lang="en">
<head>
<meta charset="utf-8">
<title>RB Tolvane – Business Card</title>
<link rel="stylesheet" href="https://fonts.googleapis.com/css2?family=Jost:wght@400;600&display=swap">
<style>
  :root {
    --brand-red: #ec1f27;
    --ink: #1d1d1d;
    --text-grey: #3a3a3a;
    --divider: #b5b5b5;
    --card-white: #ffffff;
    --backdrop: #e4e5ea;
  }
  * { box-sizing: border-box; margin: 0; padding: 0; }
  html, body {
    width: 1200px; height: 987px; overflow: hidden;
    background: var(--backdrop);
    font-family: "Jost", sans-serif;
  }
  .canvas { position: relative; width: 1200px; height: 987px; }
  .card {
    position: absolute; width: 700px; height: 400px;
    border-radius: 26px; overflow: hidden;
    box-shadow: 0 10px 28px rgba(0,0,0,0.18);
  }
  /* Back of card */
  .card-back { left: 440px; top: 60px; background: var(--brand-red); }
  .back-brand {
    position: absolute; left: 0; right: 0; top: 128px;
    display: flex; align-items: center; justify-content: center; gap: 22px;
    color: var(--card-white); font-size: 64px; font-weight: 600; letter-spacing: 1px;
    line-height: 1;
  }
  .back-brand .mark-circle {
    width: 40px; height: 40px; border-radius: 50%; background: var(--card-white);
  }
  .back-url {
    position: absolute; left: 0; right: 0; top: 276px; text-align: center;
    color: var(--card-white); font-size: 22px; letter-spacing: 6px;
  }
  /* Front of card */
  .card-front { left: 60px; top: 520px; background: var(--card-white); }
  .front-swoosh { position: absolute; inset: 0; }
  .brand-block { position: absolute; left: 40px; top: 84px; width: 300px; }
  .brand-name {
    display: flex; align-items: center; gap: 12px;
    font-size: 42px; font-weight: 600; color: var(--brand-red); line-height: 1;
  }
  .brand-name .mark-circle { width: 22px; height: 22px; border-radius: 50%; background: var(--ink); }
  .brand-tagline {
    margin-top: 10px; padding-top: 5px; border-top: 1.5px solid var(--ink);
    font-size: 17px; color: var(--ink); letter-spacing: 0.3px;
  }
  .divider {
    position: absolute; left: 360px; top: 48px; width: 1.5px; height: 170px;
    background: linear-gradient(var(--divider), rgba(181,181,181,0));
  }
  .contact-block { position: absolute; left: 385px; top: 42px; }
  .person-name { font-size: 30px; font-weight: 600; color: var(--brand-red); line-height: 1.05; }
  .person-title { font-size: 20px; color: var(--text-grey); margin-bottom: 10px; }
  .contact-list { list-style: none; }
  .contact-list li {
    display: flex; align-items: center; gap: 10px;
    font-size: 20px; color: var(--text-grey); line-height: 1.45;
  }
  .contact-list svg { width: 15px; height: 15px; flex: none; }
  .address {
    position: absolute; right: 44px; bottom: 26px; text-align: right;
    color: var(--card-white); font-size: 20px; line-height: 1.35; font-style: normal;
  }
</style>
</head>
<body>
<main class="canvas">
  <section class="card card-back" aria-label="Card back">
    <div class="back-brand"><span class="mark-circle"></span>RB Tolvane</div>
    <p class="back-url">www.rbtolvane.com</p>
  </section>

  <section class="card card-front" aria-label="Card front">
    <svg class="front-swoosh" viewBox="0 0 700 400" aria-hidden="true">
      <path d="M0 40 C0 120 0 200 0 220 C60 200 120 205 200 230 C380 285 560 320 700 330 L700 400 L0 400 Z" fill="var(--brand-red)"/>
      <path d="M0 0 L0 205 C50 120 30 60 0 0 Z" fill="var(--card-white)"/>
      <path d="M80 226 C240 250 450 300 700 318" fill="none" stroke="var(--ink)" stroke-width="3"/>
    </svg>

    <div class="brand-block">
      <div class="brand-name"><span class="mark-circle"></span>RB Tolvane</div>
      <p class="brand-tagline">spaces built without worry</p>
    </div>

    <div class="divider"></div>

    <div class="contact-block">
      <p class="person-name">Your Name</p>
      <p class="person-title">Title</p>
      <ul class="contact-list">
        <li>
          <svg viewBox="0 0 16 16"><circle cx="8" cy="8" r="8" fill="var(--brand-red)"/><path d="M5 4.5 L6.6 4.2 L7.3 6.2 L6.3 7 Q7 8.8 9 9.7 L9.8 8.7 L11.8 9.4 L11.5 11 Q7.5 11.5 5 4.5 Z" fill="#fff"/></svg>
          234-517-8062
        </li>
        <li>
          <svg viewBox="0 0 16 16"><rect x="4" y="1" width="8" height="14" rx="1.5" fill="var(--brand-red)"/><rect x="5.5" y="3" width="5" height="6" fill="#fff"/></svg>
          567-196-2043
        </li>
        <li>
          <svg viewBox="0 0 16 16"><rect x="1" y="3" width="14" height="10" rx="1" fill="var(--brand-red)"/><path d="M1.5 3.8 L8 9 L14.5 3.8" fill="none" stroke="#fff" stroke-width="1.3"/></svg>
          info@rbtolvane.com
        </li>
        <li>
          <svg viewBox="0 0 16 16"><circle cx="8" cy="8" r="7" fill="var(--brand-red)"/><path d="M1 8 H15 M8 1 V15 M8 1 Q3 8 8 15 M8 1 Q13 8 8 15" fill="none" stroke="#fff" stroke-width="0.9"/></svg>
          www.rbtolvane.com
        </li>
      </ul>
    </div>

    <address class="address">
      Door No, Street Name<br>
      City Name, State, Zip Code
    </address>
  </section>
</main>
</body>
</html>
```